NEW Modern Sleek Business Card for VR Language Startup

Our startup is using VR to lead the next wave of world language education. We need a two-sided business card that introduces the larger organization (Brightloom Language Inc) and our contact info on one side and shows the product, Glimwoorld, on the other side.

Side 1 (contact info)= Brightloom Logo and Contact info (name, title, phone, email)

Side 2 (product)= Glimworld logo, text, and website
Text= Culturally Immersive Language Learning Games
Website= www.glimworld-play.com

Target Market(s)

Education, Technology

Contact Information for Business Card

Contact info will be updated upon approval of the design. For now, put this as a placeholder.

Perry Dunmore
Founder & CEO
pdunmore@quillpost-mail.net
(555)-014-2286

Font styles to use
Other font styles liked:
• Gibson and Century Gothic are the brand fonts

Requirements
Nice to have
• I would love to see cohesion between the design and colors of the two logos. I have attached a few business card designs that I like, so you can get a feel for my preferred style.

```html
<!DOCTYPE html>
<html lang="en">
<head>
<meta charset="UTF-8">
<title>Brightloom Language – Business Card</title>
<link rel="stylesheet" href="https://fonts.googleapis.com/css2?family=Lato:wght@400;700&display=swap">
<style>
  :root {
    --backdrop: #2b2b2d;
    --card: #0d0d0e;
    --card-edge: #1a1a1c;
    --accent-orange: #f0733f;
    --accent-violet: #6a6cf0;
    --accent-cyan: #33c2f0;
    --accent-blue: #3a7bf2;
    --text-light: #f2f2f2;
    --text-muted: #a9a9ad;
    --text-dim: #5e5e62;
  }
  * { box-sizing: border-box; margin: 0; padding: 0; }
  html, body {
    width: 1200px; height: 900px; overflow: hidden;
    background: var(--backdrop);
    font-family: "Lato", "Helvetica Neue", Arial, sans-serif;
  }
  .sheet {
    width: 1200px; height: 900px;
    display: flex; flex-direction: column; align-items: center; justify-content: center;
    gap: 40px;
  }
  .card {
    position: relative;
    width: 680px; height: 390px;
    background: linear-gradient(160deg, var(--card-edge), var(--card) 60%);
    overflow: hidden;
    box-shadow: 0 14px 30px rgba(0,0,0,.45);
  }
  .card__stripe {
    position: absolute; left: 0; right: 0; bottom: 0; height: 12px;
    background: linear-gradient(to bottom, var(--accent-orange) 0 50%, var(--accent-violet) 50% 100%);
  }

  /* Product side */
  .product {
    display: flex; flex-direction: column; align-items: center; justify-content: center;
    padding-bottom: 20px;
  }
  .product__mark {
    display: flex; align-items: center; gap: 14px;
    margin-bottom: 22px;
  }
  .product__dot {
    width: 54px; height: 54px; border-radius: 50%;
    background: var(--accent-cyan);
  }
  .product__name {
    font-size: 46px; font-weight: 700; letter-spacing: 1px;
    color: var(--accent-cyan);
  }
  .product__tagline {
    text-align: center; text-transform: uppercase;
    color: var(--text-muted); font-size: 19px; font-weight: 700; line-height: 1.2;
    letter-spacing: .5px;
  }
  .product__site {
    margin-top: 14px; font-size: 18px; letter-spacing: 1.5px;
    color: var(--accent-blue);
  }

  /* Contact side */
  .contact__brand {
    position: absolute; top: 110px; left: 0; right: 0;
    display: flex; justify-content: center; align-items: center; gap: 16px;
  }
  .contact__dot {
    width: 60px; height: 60px; border-radius: 50%;
    background: var(--accent-orange);
  }
  .contact__name-brand {
    font-size: 46px; font-weight: 700; letter-spacing: 5px;
    color: var(--text-light); text-transform: uppercase;
  }
  .contact__details {
    position: absolute; top: 238px; left: 110px; right: 40px;
    display: flex; align-items: center;
  }
  .contact__person { text-align: right; padding-right: 24px; }
  .contact__person-name {
    font-size: 22px; font-weight: 700; text-transform: uppercase;
    background: linear-gradient(90deg, var(--accent-orange), var(--accent-violet));
    -webkit-background-clip: text; background-clip: text; color: transparent;
  }
  .contact__role { font-size: 17px; color: var(--text-light); }
  .contact__divider { width: 1px; height: 56px; background: var(--text-dim); }
  .contact__lines { padding-left: 22px; display: flex; flex-direction: column; gap: 6px; }
  .contact__line {
    display: flex; align-items: center; gap: 8px;
    font-size: 17px; color: var(--text-light);
  }
  .contact__icon { width: 16px; height: 16px; flex: none; }
</style>
</head>
<body>
<main class="sheet">
  <section class="card product" aria-label="Product side">
    <div class="product__mark">
      <span class="product__dot"></span>
      <span class="product__name">Glimworld</span>
    </div>
    <p class="product__tagline">Culturally Immersive<br>Language Learning Games</p>
    <p class="product__site">www.glimworld-play.com</p>
    <div class="card__stripe"></div>
  </section>

  <section class="card contact" aria-label="Contact side">
    <div class="contact__brand">
      <span class="contact__dot"></span>
      <span class="contact__name-brand">Brightloom</span>
    </div>
    <div class="contact__details">
      <div class="contact__person">
        <p class="contact__person-name">Perry Dunmore</p>
        <p class="contact__role">Founder &amp; CEO</p>
      </div>
      <span class="contact__divider"></span>
      <div class="contact__lines">
        <p class="contact__line">
          <svg class="contact__icon" viewBox="0 0 16 16" aria-hidden="true">
            <path d="M3 2h3l1 3-2 1.5a9 9 0 0 0 4.5 4.5L11 9l3 1v3a1.5 1.5 0 0 1-1.5 1.5A11.5 11.5 0 0 1 1.5 3.5 1.5 1.5 0 0 1 3 2z" fill="#f0733f"/>
          </svg>
          (555)-014-2286
        </p>
        <p class="contact__line">
          <svg class="contact__icon" viewBox="0 0 16 16" aria-hidden="true">
            <rect x="1" y="3" width="14" height="10" rx="1" fill="#6a6cf0"/>
            <path d="M1.5 3.5 8 9l6.5-5.5" fill="none" stroke="#0d0d0e" stroke-width="1.3"/>
          </svg>
          pdunmore@quillpost-mail.net
        </p>
      </div>
    </div>
    <div class="card__stripe"></div>
  </section>
</main>
</body>
</html>
```